HAIR EXTENSIONS

We need a web design for a company base in Chicago called Tresses by Jolavie. We sale 100% human hair in Brazilian body wave deep wave straight or natural curl, Peruvian body wave straight or deep wave. Malaysian loose straight or body wave, in the chicago land.
We also ship hair to any city or country. We like to see design that use the colors pinks & grays, or would just like to see some design creative with colors thats inviting.

Also I'm using the quillmoss template, Home- banner contact us, about us, Features- product side/left sidebar, Shop- wish list /shopping cart/ tracking your order / checkout/ order received.
Porfolio-filterable 4column portfolio
Blog. Buy now

Industry/Entity Type

Hair

Number of Pages Required

4 page

Colors
aaaaaa
606060
dddddd
eea4c8
d3a5cc
b868aa
a6459a
ffc213
1b1b1b

Requirements
Must have
• I NEED THE DESIGNER TO DO THE 4 PAGE LIKE THIS.
• 1.HOME-PAGE BANNER CONTACT US SOME PRODUCT WITH SIDING IMAGES OF THE TOP PROUDCT
• 2.PRODUCT WITH SHOPPING CART- I WANT SIDING BARS FOR PRODUCT & SHOPPING CART WITH TRACKING YOUR ORDERS CHECK OUT & ORDER RECEIVED.
• 3.PORFOLIO PHOTO-I WANT A FEATURES FOR CUSTOMERS TO UPLOAN THERE PICTURE & BLOG ON THE PAGE
• 4.ABOUT US- TALK ABOUT ARE COMPAMY.
Nice to have
• hello designer
• I was working with a web developer for my site be for i came to craftnookly & they build a site for me that i liked, You all can view it at www.Tressesbyjolavie.info
• long story short never could get them to finish the project after they got paid!!
• I know, why paid before its finish bad decision. So know I'm here starting over with you all.
• here is a list of my competition site
• www.lockswellhub.com
• www.vanoraloft.com
• www.pellinoshop.com
• So just to give some insight, I'm looking for something like the one i had builded.

```html
<!DOCTYPE html>
<html lang="en">
<head>
<meta charset="utf-8">
<title>Tresses by Jolavie — Hair Extensions</title>
<link href="https://fonts.googleapis.com/css2?family=Source+Sans+3:wght@400;600;700&display=swap" rel="stylesheet">
<style>
:root{
  --orange:#e8821e;
  --blue:#3f6f92;
  --ink:#1b1b1b;
  --text:#606060;
  --muted:#aaaaaa;
  --line:#dddddd;
  --footer:#2a2a2a;
  --footer-deep:#1f1f1f;
  --white:#ffffff;
}
*{box-sizing:border-box;margin:0;padding:0}
html,body{width:704px;height:1200px;overflow:hidden;background:var(--white)}
body{font-family:"Source Sans 3",sans-serif;color:var(--text);position:relative}
.abs{position:absolute}

/* header */
.brand{left:82px;top:22px;display:flex;align-items:center;gap:7px;font-size:17px;font-weight:600;color:var(--ink)}
.brand-mark{width:11px;height:11px;background:var(--orange);display:block}
.phone{left:430px;top:20px;width:98px;height:20px;background:#6b8aa3;color:var(--white);font-size:9px;display:flex;align-items:center}
.phone .ico{width:22px;height:20px;background:var(--blue);display:flex;align-items:center;justify-content:center;margin-right:10px}
.account{left:535px;top:20px;width:86px;height:20px;background:var(--orange);color:var(--white);font-size:7px;display:flex;align-items:center;justify-content:center;border:1px solid #f3a75a}

/* nav */
.nav{left:0;top:68px;width:704px;height:45px;background:var(--orange)}
.nav ul{list-style:none;position:absolute;left:83px;top:17px;display:flex;gap:20px}
.nav li{color:var(--white);font-size:9px;font-weight:600}
.search{left:426px;top:80px;width:128px;height:23px;background:var(--white);border-radius:2px}
.search svg{position:absolute;right:8px;top:6px}
.login{left:561px;top:80px;width:60px;height:23px;border:2px solid var(--white);color:var(--white);font-size:10px;font-weight:700;display:flex;align-items:center;justify-content:center;border-radius:2px}

/* hero */
.hero{left:0;top:113px;width:704px;height:305px;background:linear-gradient(90deg,#d9d9d6 0%,#a7a39c 28%,#4a3a30 40%,#3a2b22 60%,#5a4232 80%,#6a4d38 100%)}
.hero-title{left:0;top:222px;width:704px;text-align:center;color:var(--orange);font-size:20px;font-weight:400;letter-spacing:-.5px}
.hero-text{left:0;top:262px;width:704px;text-align:center;color:var(--white);font-size:11.5px;line-height:21px;font-weight:600}
.hero-btn{left:296px;top:318px;width:112px;height:30px;background:var(--orange);border:2px solid var(--white);border-radius:10px;color:var(--white);font-size:11px;font-weight:700;display:flex;align-items:center;justify-content:center}
.dots{left:327px;top:374px;display:flex;gap:5px}
.dots i{width:6px;height:6px;border-radius:50%;background:var(--orange);display:block}
.dots i.on{background:transparent;border:1px solid var(--orange)}

/* promos */
.promo{top:455px;height:66px;border:1px dashed #888;text-align:center;padding-top:14px}
.promo h3{color:var(--orange);font-size:13px;font-weight:400}
.promo p{color:var(--ink);font-size:9px;font-weight:400;margin-top:5px}

/* products */
.product{top:564px;width:125px}
.product .photo{width:125px;height:145px}
.product .cat{font-size:5.5px;color:#bbb;text-align:center;margin-top:9px;letter-spacing:.2px}
.product .info{border:1px solid var(--line);height:75px;margin-top:3px;text-align:center;position:relative}
.product h4{font-size:10.5px;font-weight:400;color:var(--ink);margin-top:13px}
.product small{display:block;font-size:7px;font-weight:400;color:var(--text);margin-top:1px}
.product .price{position:absolute;left:13px;bottom:10px;color:var(--orange);font-size:8px}
.product .sep{position:absolute;left:61px;bottom:6px;width:1px;height:20px;background:var(--line)}
.product .acts{position:absolute;right:16px;bottom:9px}

/* news */
.news-rule{left:82px;top:820px;width:490px;height:1px;background:var(--line)}
.news-rule b{position:absolute;left:0;top:-1px;width:42px;height:3px;background:var(--orange)}
.news-title{left:83px;top:830px;font-size:13px;color:var(--ink);font-weight:600}
.arrow{top:820px;width:22px;height:19px;border:1px solid #999;display:flex;align-items:center;justify-content:center}
.news{top:861px;width:166px}
.news .photo{height:85px;border:2px solid var(--line)}
.news h5{font-size:11px;font-weight:400;color:var(--ink);margin-top:10px}
.news .meta{font-size:5px;color:var(--text);margin-top:4px}
.news p{font-size:6.5px;line-height:12px;color:#888;margin-top:2px}

/* footer */
.footer{left:0;top:1034px;width:704px;height:132px;background:var(--footer)}
.col{top:1048px;color:#cfcfcf}
.col h6{font-size:10px;font-weight:400;color:#bbb;margin-bottom:8px}
.col li{list-style:none;font-size:6.5px;font-weight:400;line-height:15.4px}
.col p{font-size:6.5px;font-weight:400;line-height:12px}
.col .posted{margin:5px 0 11px;display:flex;align-items:center;gap:4px}
.vline{top:1050px;width:1px;height:104px;background:#444}
.social li{display:flex;align-items:center;gap:8px;line-height:normal;margin-bottom:4px}
.social i{width:16px;height:16px;border-radius:50%;background:#e8e8e8;display:block}
.bottom{left:0;top:1166px;width:704px;height:34px;background:var(--footer-deep)}
.copy{left:84px;top:1181px;font-size:5.5px;color:#777}
</style>
</head>
<body>

<header>
  <div class="abs brand"><span class="brand-mark"></span>Tresses by Jolavie</div>
  <div class="abs phone"><span class="ico"><svg width="9" height="9" viewBox="0 0 24 24"><path fill="#fff" d="M6.6 10.8a15 15 0 006.6 6.6l2.2-2.2c.3-.3.7-.4 1-.2 1.1.4 2.3.6 3.6.6.6 0 1 .4 1 1V20c0 .6-.4 1-1 1A17 17 0 013 4c0-.6.4-1 1-1h3.5c.6 0 1 .4 1 1 0 1.3.2 2.5.6 3.6.1.3 0 .7-.2 1z"/></svg></span>555 014 2286</div>
  <div class="abs account">✓ &nbsp;MY ACCOUNT &nbsp;&gt;&gt;</div>
</header>

<nav class="abs nav">
  <ul><li>HOME</li><li>THEME FEATURES</li><li>SHOP</li><li>PORTFOLIO</li><li>BLOG</li><li>CONTACT</li></ul>
</nav>
<div class="abs search"><svg width="10" height="10" viewBox="0 0 10 10"><circle cx="4" cy="4" r="3" fill="none" stroke="#555" stroke-width="1.4"/><line x1="6.2" y1="6.2" x2="9" y2="9" stroke="#555" stroke-width="1.6"/></svg></div>
<div class="abs login">LOGIN</div>

<section>
  <div class="abs hero" role="img" aria-label="Graduate in cap and gown holding a diploma, wearing long hair extensions"></div>
  <h1 class="abs hero-title">LOREM IPSUM DOLOR SIT AMET ?</h1>
  <p class="abs hero-text">Sed ut perspiciatis unde omnis iste natus error sit voluptatem accusantium doloremque laudantium,<br>totam rem aperiam, eaque ipsa quae ab illo inventore veritatis et quasi</p>
  <div class="abs hero-btn">LEARN MORE</div>
  <div class="abs dots"><i></i><i></i><i></i><i class="on"></i><i></i></div>
</section>

<section>
  <div class="abs promo" style="left:84px;width:247px"><h3>GET 25% OFF WHEN YOU SPEND $100</h3><p>LIMITED TIME ONLY | USE CODE: BYJOLAVIE</p></div>
  <div class="abs promo" style="left:373px;width:248px"><h3>FREE SHIPPING ON ALL ORDERS</h3><p>FREE OVER $125 FOR INTERNATIONAL ORDERS</p></div>
</section>

<section>
  <div class="abs product" style="left:82px">
    <div class="photo" role="img" aria-label="Customer wearing curly hair extensions with a lilac scarf" style="background:linear-gradient(180deg,#c9c4c4,#8e6c8f 70%,#b58cc0)"></div>
    <div class="cat">BRAZILIAN BODY WAVE</div>
    <div class="info"><h4>CONSECTETUER ADIPIS</h4><small>LOREM IPSUM DOLO</small><span class="price">$ 70.00</span><span class="sep"></span>
      <svg class="acts" width="28" height="10" viewBox="0 0 28 10"><path d="M5 9L1 5a2.2 2.2 0 014-3 2.2 2.2 0 014 3z" fill="none" stroke="#999"/><circle cx="22" cy="5" r="4" fill="none" stroke="#999"/><path d="M20 5h4M22 3v4" stroke="#999"/></svg></div>
  </div>
  <div class="abs product" style="left:220px">
    <div class="photo" role="img" aria-label="Customer in a fur coat with long wavy extensions" style="background:linear-gradient(180deg,#9fb3bf,#8a7350 55%,#b89a6c)"></div>
    <div class="cat">BRAZILIAN BODY WAVE</div>
    <div class="info"><h4>CONSECTETUER ADIPIS</h4><small>LOREM IPSUM DOLO</small><span class="price">$ 70.00</span><span class="sep"></span>
      <svg class="acts" width="28" height="10" viewBox="0 0 28 10"><path d="M5 9L1 5a2.2 2.2 0 014-3 2.2 2.2 0 014 3z" fill="none" stroke="#999"/><circle cx="22" cy="5" r="4" fill="none" stroke="#999"/><path d="M20 5h4M22 3v4" stroke="#999"/></svg></div>
  </div>
  <div class="abs product" style="left:358px">
    <div class="photo" role="img" aria-label="Customer in a car with a straight bob style" style="background:linear-gradient(180deg,#d6dbe0,#5a4a45 45%,#7f9ac4)"></div>
    <div class="cat">BRAZILIAN BODY WAVE</div>
    <div class="info"><h4>CONSECTETUER ADIPIS</h4><small>LOREM IPSUM DOLO</small><span class="price">$ 70.00</span><span class="sep"></span>
      <svg class="acts" width="28" height="10" viewBox="0 0 28 10"><path d="M5 9L1 5a2.2 2.2 0 014-3 2.2 2.2 0 014 3z" fill="none" stroke="#999"/><circle cx="22" cy="5" r="4" fill="none" stroke="#999"/><path d="M20 5h4M22 3v4" stroke="#999"/></svg></div>
  </div>
  <div class="abs product" style="left:496px">
    <div class="photo" role="img" aria-label="Customer standing in a room wearing long curly extensions and a blue top" style="background:linear-gradient(180deg,#5f5a45,#3b3a2d 40%,#3b4fa0 70%,#3a3530)"></div>
    <div class="cat">BRAZILIAN BODY WAVE</div>
    <div class="info"><h4>CONSECTETUER ADIPIS</h4><small>LOREM IPSUM DOLO</small><span class="price">$ 70.00</span><span class="sep"></span>
      <svg class="acts" width="28" height="10" viewBox="0 0 28 10"><path d="M5 9L1 5a2.2 2.2 0 014-3 2.2 2.2 0 014 3z" fill="none" stroke="#999"/><circle cx="22" cy="5" r="4" fill="none" stroke="#999"/><path d="M20 5h4M22 3v4" stroke="#999"/></svg></div>
  </div>
</section>

<section>
  <div class="abs news-rule"><b></b></div>
  <h2 class="abs news-title">LATEST NEWS</h2>
  <div class="abs arrow" style="left:578px"><svg width="6" height="8"><path d="M5 1L1 4l4 3" fill="none" stroke="#333"/></svg></div>
  <div class="abs arrow" style="left:599px"><svg width="6" height="8"><path d="M1 1l4 3-4 3" fill="none" stroke="#333"/></svg></div>

  <article class="abs news" style="left:82px">
    <div class="photo" role="img" aria-label="Customer with voluminous curls in a kitchen" style="background:linear-gradient(90deg,#a8703a,#3a2a24 50%,#9a6a3a)"></div>
    <h5>Lorem ipsum dolor sit amet.</h5><div class="meta">0 Comments</div>
    <p>Sed ut perspiciatis unde omnis iste natus error sit voluptatem accusantium doloremque laudantium Donec quam felis, ultricies nec.</p>
  </article>
  <article class="abs news" style="left:269px">
    <div class="photo" role="img" aria-label="Graduate in cap and gown holding a diploma" style="background:linear-gradient(90deg,#e0e0dc,#6a5040 40%,#2a2420 60%,#6a4d38)"></div>
    <h5>Lorem ipsum dolor sit amet.</h5><div class="meta">0 Comments</div>
    <p>Sed ut perspiciatis unde omnis iste natus error sit voluptatem accusantium doloremque laudantium Donec quam felis, ultricies nec.</p>
  </article>
  <article class="abs news" style="left:456px">
    <div class="photo" role="img" aria-label="Back view of long curly extensions in a kitchen" style="background:linear-gradient(90deg,#a87a48,#2a3a5a 50%,#a87a48)"></div>
    <h5>Lorem ipsum dolor sit amet.</h5><div class="meta">0 Comments</div>
    <p>Sed ut perspiciatis unde omnis iste natus error sit voluptatem accusantium doloremque laudantium Donec quam felis, ultricies nec.</p>
  </article>
</section>

<footer>
  <div class="abs footer"></div>
  <div class="abs col" style="left:87px"><h6>COMPANY</h6><ul><li>COMPANY OVERVIEW</li><li>ABOUT US</li><li>SERVICES PROVIDE</li><li>OUR PROCESS</li><li>OUR CLIENTS</li></ul></div>
  <div class="abs vline" style="left:179px"></div>
  <div class="abs col" style="left:207px"><h6>WHAT WE DO</h6><ul><li>VALUE PROPOSITION</li><li>OUR WORK</li><li>TESTIMONIALS</li><li>FAQ</li><li>CONTACT US</li></ul></div>
  <div class="abs vline" style="left:302px"></div>
  <div class="abs col" style="left:329px;width:160px"><h6>CHIRPLY FEED</h6>
    <p>Nunc tempus felis vitae urna. Vivamus porttitor, g, purus nisi eleifend libero, a tempus</p>
    <p class="posted">Posted 3 hours ago <svg width="10" height="8"><path d="M1 4l3 3 5-6" fill="none" stroke="#eee" stroke-width="1.5"/></svg></p>
    <p>Nunc tempus felis vitae urna. Vivamus porttitor, g, purus nisi eleifend libero, a tempus</p>
    <p class="posted">Posted 3 hours ago <svg width="10" height="8"><path d="M1 4l3 3 5-6" fill="none" stroke="#eee" stroke-width="1.5"/></svg></p>
  </div>
  <div class="abs vline" style="left:510px"></div>
  <div class="abs col social" style="left:543px"><h6>GET CONNECTED</h6><ul><li><i></i>Friendsy</li><li><i></i>Chirply</li><li><i></i>Linkwork</li><li><i></i>RSS</li></ul></div>
  <div class="abs bottom"></div>
  <div class="abs copy">© 2014 Company Name. &nbsp;All right reserved. &nbsp;Term of Use</div>
</footer>

</body>
</html>
```